Homemaking training schools needs a Business Card design

Designer, Hello!

No special requirements, good-looking enough.
--------------------------------------------------------------------------

Name: Marcus Dole
Chairman
Tel: 0574-71948263
Mobile: 13857420916
Email: kelvora@mailnest.example
Web: www.prt2019.example
Add: No.258, LanpingJie, BeiyuanQu, Ningbo, Zhejiang

LOGO
Ningbo PRT Homemaking Training School

Target Market(s)

pregnant women, mothers, infants, the elderly and families, including cleaning, cooking, nursing training.

Industry/Entity Type

Business

Contact Information for Business Card

Name: Marcus Dole
Chairman
Tel: 0574-71948263
Mobile: 13857420916
Email: kelvora@mailnest.example
Web: www.prt2019.example

LOGO

Font styles to use
Serif
Sans Serif
Decorative

Requirements
Nice to have
• Feels: clean, specifications, safety, comfort, warmth and happiness.

```html
<!DOCTYPE html>
<html lang="en">
<head>
<meta charset="utf-8">
<title>PeiRenTang Training &amp; Services – Business Card</title>
<link rel="stylesheet" href="https://fonts.googleapis.com/css2?family=Roboto:wght@400;700&display=swap">
<style>
  :root {
    --magenta: #e8168b;
    --blue: #1f78c6;
    --ink: #4a4a4a;
    --rule: #8a8a8a;
    --white: #ffffff;
    --backdrop: #e7e4df;
  }
  * { box-sizing: border-box; margin: 0; padding: 0; }
  html, body { width: 1200px; height: 950px; overflow: hidden; }
  body {
    background: var(--backdrop);
    font-family: "Roboto", Arial, sans-serif;
    position: relative;
  }
  .card {
    position: absolute;
    left: 290px;
    width: 620px;
    height: 354px;
    box-shadow: 0 8px 24px rgba(0,0,0,.18);
    overflow: hidden;
  }
  .card--front { top: 90px; background: var(--magenta); color: var(--white); }
  .card--back { top: 506px; background: var(--white); }

  .brand { position: absolute; text-align: center; }
  .brand__name {
    display: block;
    font-family: "Roboto", Arial, sans-serif;
    font-weight: 700;
    line-height: 1;
  }
  .brand__tagline {
    display: block;
    font-weight: 400;
    margin: 8px auto 0;
    padding-bottom: 5px;
  }

  .card--front .brand { left: 0; right: 0; top: 112px; }
  .card--front .brand__name { font-size: 44px; color: var(--white); }
  .card--front .brand__tagline {
    font-size: 17px; width: 250px;
    border-bottom: 1.5px solid var(--white);
  }
  .front__web {
    position: absolute; left: 0; right: 0; top: 262px;
    text-align: center; font-size: 13px; letter-spacing: 5px;
  }

  .card--back .brand { left: 60px; top: 94px; width: 300px; }
  .card--back .brand__name { font-size: 34px; color: var(--blue); }
  .card--back .brand__tagline {
    font-size: 14px; color: var(--ink); width: 210px;
    border-bottom: 1.5px solid var(--rule);
  }

  .tab { position: absolute; width: 9px; height: 100px; background: var(--blue); border-radius: 6px; }
  .tab--right { right: -3px; top: 28px; }
  .tab--left { left: -3px; bottom: 22px; }

  .contact {
    position: absolute; right: 26px; top: 40px;
    list-style: none; text-align: right;
    font-size: 13.5px; color: var(--ink); line-height: 21px;
  }
  .contact li { display: flex; justify-content: flex-end; align-items: center; gap: 8px; }
  .contact svg { width: 13px; height: 13px; fill: var(--blue); flex: none; }
  .contact .icon-web { fill: none; stroke: var(--blue); stroke-width: 1.4; }

  .person { position: absolute; left: 60px; top: 232px; }
  .person__name { font-size: 19px; font-weight: 700; color: var(--blue); }
  .person__title { font-size: 13px; color: var(--magenta); margin-top: 3px; }
  .person__address { font-size: 13px; color: var(--ink); line-height: 19px; margin-top: 10px; font-style: normal; }
</style>
</head>
<body>
  <section class="card card--front" aria-label="Card front">
    <div class="brand">
      <span class="brand__name">PeiRenTang</span>
      <span class="brand__tagline">Training &amp; Services</span>
    </div>
    <p class="front__web">www.prt2019.example</p>
  </section>

  <section class="card card--back" aria-label="Card back">
    <span class="tab tab--right"></span>
    <span class="tab tab--left"></span>

    <div class="brand">
      <span class="brand__name">PeiRenTang</span>
      <span class="brand__tagline">Training &amp; Services</span>
    </div>

    <ul class="contact">
      <li>0574-71948263
        <svg viewBox="0 0 16 16" aria-hidden="true"><path d="M3 1h3l1.5 4-2 1.3a9 9 0 0 0 4.2 4.2L11 8.5l4 1.5v3a2 2 0 0 1-2 2A12 12 0 0 1 1 3a2 2 0 0 1 2-2z"/></svg></li>
      <li>13857420916
        <svg viewBox="0 0 16 16" aria-hidden="true"><path d="M4.5 0h7A1.5 1.5 0 0 1 13 1.5v13a1.5 1.5 0 0 1-1.5 1.5h-7A1.5 1.5 0 0 1 3 14.5v-13A1.5 1.5 0 0 1 4.5 0zM5 2v10h6V2zm3 11a1 1 0 1 0 0 2 1 1 0 0 0 0-2z"/></svg></li>
      <li>kelvora@mailnest.example
        <svg viewBox="0 0 16 16" aria-hidden="true"><path d="M1 3h14v10H1zm1.5 1.2L8 8.5l5.5-4.3z"/></svg></li>
      <li>www.prt2019.example
        <svg class="icon-web" viewBox="0 0 16 16" aria-hidden="true"><circle cx="8" cy="8" r="6.8"/><ellipse cx="8" cy="8" rx="3" ry="6.8"/><path d="M1.2 8h13.6"/></svg></li>
    </ul>

    <div class="person">
      <h1 class="person__name">Marcus Dole</h1>
      <p class="person__title">Chairman</p>
      <address class="person__address">No.258, LanpingJie<br>BeiyuanQu, Ningbo, Zhejiang</address>
    </div>
  </section>
</body>
</html>
```